Business Cards Needed for Innovative Healthcare Marketing Company

We are a marketing company focused on healthcare. Our company is all about rebranding yourself renewing your image and generating results. The phoenix stands for "reborn" or "rising" which we provide new brands for our clients we take their old brands and renew it with creativity and innovation. I am looking for a business card with color dimension. I have attached an example of a card I think has the look and feel of what I am trying to accomplish. I like that the card example has black and grey font colors, I like the font placement and the small logo, I really like the use of the colors on the right those are the colors of my logo. My logo is phoenix so maybe incorporating flames similar to that design. I would like the back a solid color maybe red with an opaque version of the logo and website. As a marketing company I am always open to creative liberty!

Target Market(s)

Doctors and business professionals.

Industry/Entity Type

Marketing

Contact Information for Business Card

Valcorne Health Care Marketing
Marla Tenwick- CEO
#(512)638-2974
email-marla@valcorne.com
website- valcorne.com

Font styles to use
Sans Serif

Colors
ec1f27
f37122
ffc214
fbed22
fbf289
f04a50

Requirements
Must have
• The logo and required information
Nice to have
• icons by the information
Should not have
• child like font

```html
<!DOCTYPE html>
<html lang="en">
<head>
<meta charset="utf-8">
<title>Valcorne Health Care Marketing – Business Card</title>
<link href="https://fonts.googleapis.com/css2?family=Open+Sans:ital,wght@0,300;0,400;0,600;0,700;1,400&display=swap" rel="stylesheet">
<style>
  :root {
    --stage: #9b9c9e;
    --paper: #f3f3f5;
    --crimson: #8e1b1f;
    --crimson-deep: #861a1e;
    --ember: #d9781f;
    --flame: #e9891c;
    --ink: #3a3a3c;
    --rule: #8a8a8c;
    --white: #ffffff;
  }
  * { box-sizing: border-box; margin: 0; padding: 0; }
  html, body {
    width: 1105px;
    height: 1200px;
    overflow: hidden;
  }
  body {
    background: var(--stage);
    font-family: "Open Sans", Arial, sans-serif;
    position: relative;
  }
  .card {
    position: absolute;
    left: 180px;
    width: 746px;
    height: 425px;
    overflow: hidden;
  }
  .card--front { top: 120px; background: var(--paper); }
  .card--back {
    top: 637px;
    background: radial-gradient(ellipse 60% 70% at 50% 42%, var(--flame) 0%, #b9531f 55%, var(--crimson-deep) 100%);
  }

  /* Front: brand block */
  .brand {
    position: absolute;
    left: 318px;
    top: 60px;
    display: flex;
    align-items: center;
    gap: 18px;
  }
  .brand__dot {
    width: 120px;
    height: 120px;
    border-radius: 50%;
    background: var(--ember);
    flex: none;
  }
  .brand__name {
    color: var(--crimson);
    font-weight: 300;
    line-height: 1;
  }
  .brand__name-main {
    display: block;
    font-size: 42px;
    letter-spacing: 1px;
  }
  .brand__name-sub {
    display: block;
    margin-top: 10px;
    padding-top: 6px;
    border-top: 1px solid var(--rule);
    font-size: 15px;
    letter-spacing: 0.6px;
  }

  /* Front: person */
  .person {
    position: absolute;
    left: 55px;
    top: 240px;
    right: 61px;
  }
  .person__name {
    color: var(--crimson);
    font-size: 25px;
    font-weight: 700;
    letter-spacing: 0.4px;
  }
  .person__role {
    display: flex;
    align-items: center;
    gap: 10px;
    color: var(--flame);
    font-size: 19px;
    font-weight: 400;
    line-height: 1;
    margin-top: 2px;
  }
  .person__role::after {
    content: "";
    flex: 1;
    height: 1px;
    background: var(--rule);
  }

  .contact {
    position: absolute;
    left: 55px;
    top: 318px;
    list-style: none;
    color: var(--ink);
    font-size: 19px;
  }
  .contact__item {
    display: flex;
    align-items: center;
    gap: 12px;
    height: 29px;
  }
  .contact__icon { width: 18px; height: 18px; fill: var(--crimson); flex: none; }

  .website {
    position: absolute;
    right: 61px;
    top: 336px;
    color: var(--ink);
    font-size: 19px;
  }

  .edge-band {
    position: absolute;
    left: 0;
    bottom: 0;
    width: 100%;
    height: 16px;
    background: linear-gradient(90deg, var(--crimson) 0%, var(--crimson) 62%, #b8421c 80%, var(--flame) 100%);
  }

  /* Back */
  .back-brand {
    position: absolute;
    left: 0;
    right: 0;
    top: 140px;
    display: flex;
    flex-direction: column;
    align-items: center;
    gap: 16px;
    color: var(--white);
  }
  .back-brand__dot {
    width: 70px;
    height: 70px;
    border-radius: 50%;
    background: rgba(255,255,255,0.85);
  }
  .back-brand__name {
    font-size: 40px;
    font-weight: 300;
    letter-spacing: 2px;
    line-height: 1;
  }
  .back-website {
    position: absolute;
    left: 0;
    right: 0;
    top: 365px;
    text-align: center;
    color: var(--white);
    font-size: 20px;
    font-style: italic;
    letter-spacing: 6px;
  }
</style>
</head>
<body>

  <section class="card card--front" aria-label="Business card front">
    <div class="brand">
      <span class="brand__dot" aria-hidden="true"></span>
      <span class="brand__name">
        <span class="brand__name-main">VALCORNE</span>
        <span class="brand__name-sub">HEALTH CARE MARKETING</span>
      </span>
    </div>

    <div class="person">
      <h1 class="person__name">MARLA TENWICK</h1>
      <p class="person__role">CEO</p>
    </div>

    <ul class="contact">
      <li class="contact__item">
        <svg class="contact__icon" viewBox="0 0 24 24" aria-hidden="true">
          <path d="M6.6 10.8c1.4 2.8 3.8 5.1 6.6 6.6l2.2-2.2c.3-.3.7-.4 1-.2 1.1.4 2.3.6 3.6.6.6 0 1 .4 1 1V20c0 .6-.4 1-1 1C10.6 21 3 13.4 3 4c0-.6.4-1 1-1h3.5c.6 0 1 .4 1 1 0 1.3.2 2.5.6 3.6.1.3 0 .7-.2 1l-2.3 2.2z"/>
        </svg>
        <span>(512)638-2974</span>
      </li>
      <li class="contact__item">
        <svg class="contact__icon" viewBox="0 0 24 24" aria-hidden="true">
          <path d="M2 5h20v14H2z M3.5 6.5 12 12.5l8.5-6z" fill-rule="evenodd"/>
        </svg>
        <span>marla@valcorne.com</span>
      </li>
    </ul>

    <p class="website">www.valcorne.com</p>

    <div class="edge-band" aria-hidden="true"></div>
  </section>

  <section class="card card--back" aria-label="Business card back">
    <div class="back-brand">
      <span class="back-brand__dot" aria-hidden="true"></span>
      <span class="back-brand__name">VALCORNE</span>
    </div>
    <p class="back-website">www.valcorne.com</p>
  </section>

</body>
</html>
```